Velmora Sports Foundation website

Velmora sports foundation is a charity organisation that assists young athletes and clubs with the financial assistance they need to progress in their sporting career.

The organisation also establishes mentoring programs to community clubs and individuals.
We envision a home page with a horizontal navigation
Contact Us
Donate: A link to a secure payment system
Meet the team: A list of names and images of the board
Lastly the link to donate should be featured prominently and several times along with cues that lead people to find out more
We prefer limited scrolling and would like to see a clean yet modern design

I am unsure if it needs to be coded or not

Target Market(s)

Potential donors, applications for funds, potential affiliates

Industry/Entity Type

Charity

Coding

Coded - Design and coding required

Number of Pages Required

5+ page

Font styles to use
Sans Serif

Colors
3176b5
ec1f27
34a7d7

Requirements
Must have
• emotionally engaging and informative
• motion enabled pictures
• links to donate
• Music
• Enable video uploads
• Large horizontal pictures of young sports players prominently soccer at this stage
• Social media presence
Nice to have
• Live chat
Should not have
• Images that depict poverty

```html
<!DOCTYPE html>
<html lang="en">
<head>
<meta charset="utf-8">
<title>Velmora Sports Foundation</title>
<link rel="stylesheet" href="https://fonts.googleapis.com/css2?family=Mulish:wght@400;500;600;700;800&display=swap">
<style>
:root{
  --blue:#3176b5;
  --red:#ec1f27;
  --sky:#34a7d7;
  --navy:#2a5f9e;
  --ink:#333;
  --muted:#777;
  --line:#dcdcdc;
  --footer:#f0f0f0;
  --white:#fff;
}
*{box-sizing:border-box;margin:0;padding:0}
html,body{width:1200px;height:2281px;overflow:hidden}
body{position:relative;font-family:"Mulish",sans-serif;color:var(--ink);background:var(--white)}
.abs{position:absolute}
a{color:inherit;text-decoration:none}

/* header */
.site-header{left:0;top:0;width:1200px;height:111px;background:var(--white)}
.brand{left:137px;top:34px;display:flex;align-items:center;gap:12px}
.brand-mark{width:40px;height:40px;border-radius:50%;border:5px solid var(--blue)}
.brand-name{font-weight:800;font-size:22px;color:var(--blue);line-height:1.05;width:190px}
.main-nav{left:488px;top:47px;font-size:15.5px;color:#777}
.main-nav a{position:absolute;white-space:nowrap}
.main-nav .active{color:var(--blue)}
.nav-underline{left:482px;top:105px;width:61px;height:6px;background:var(--blue)}
.btn-donate{display:flex;align-items:center;justify-content:center;gap:8px;background:var(--red);color:var(--white);font-size:15px;border-radius:2px}
.btn-donate svg{width:22px;height:22px}

/* hero */
.hero{left:0;top:111px;width:1200px;height:548px;
  background:
    radial-gradient(ellipse 260px 200px at 4% 68%,rgba(230,235,245,.55),transparent 70%),
    radial-gradient(ellipse 380px 260px at 20% 22%,rgba(150,160,170,.55),transparent 70%),
    radial-gradient(ellipse 300px 360px at 64% 55%,rgba(215,205,190,.45),transparent 70%),
    radial-gradient(ellipse 260px 260px at 30% 62%,rgba(50,80,150,.55),transparent 70%),
    radial-gradient(ellipse at 55% 35%,#5a6470 0%,#2c323b 45%,#14181f 100%)}
.hero-title{left:0;top:310px;width:1180px;text-align:center;color:var(--white);font-weight:700;font-size:46px;letter-spacing:1px}
.hero-sub{left:0;top:379px;width:1175px;text-align:center;color:var(--white);font-weight:700;font-size:26px;letter-spacing:.5px}
.slider-dots{left:558px;top:619px;display:flex;gap:9px}
.slider-dots span{width:15px;height:15px;border-radius:50%;background:var(--white)}
.slider-dots span:first-child{background:transparent;border:2px solid var(--white)}

/* about */
.about-title{left:136px;top:737px;font-size:27px;font-weight:400;letter-spacing:1px;color:#222}
.about-text{left:137px;top:790px;width:510px;font-size:13.5px;line-height:24px;color:var(--muted)}
.about-text p+p{margin-top:12px}
.about-donate{left:132px;top:954px;width:120px;height:38px}
.video{left:666px;top:732px;width:396px;height:243px;background:#1f1f1f}
.video-frame{left:0;top:0;width:396px;height:215px;
  background:
    radial-gradient(ellipse 90px 110px at 48% 45%,rgba(240,240,245,.7),transparent 70%),
    radial-gradient(ellipse 200px 140px at 85% 40%,rgba(240,190,70,.9),transparent 70%),
    linear-gradient(180deg,#3a4560 0%,#6a6a5a 45%,#b89a48 75%,#3b5e2a 100%)}
.video-play{left:171px;top:80px;width:54px;height:54px;border-radius:50%;background:var(--white)}
.video-bar{left:0;top:215px;width:396px;height:28px;background:#2b2b2b}

/* programs */
.programs{left:0;top:1060px;width:1200px;height:397px;background:linear-gradient(180deg,var(--sky) 0%,var(--navy) 100%)}
.programs-title{left:0;top:40px;width:1200px;text-align:center;color:var(--white);font-size:34px;font-weight:400}
.programs-rule{top:62px;width:36px;height:1px;background:rgba(255,255,255,.8)}
.program-photo{width:228px;height:228px;border-radius:50%}
.program-name{color:var(--white);font-size:21px;font-weight:400}
.program-text{color:rgba(255,255,255,.9);font-size:12.5px;line-height:22.5px;width:186px}
.btn-light{display:flex;align-items:center;justify-content:center;width:118px;height:34px;background:var(--sky);color:var(--white);font-size:14px}

/* cards */
.card{top:1501px;width:301px;height:347px;border:1px solid var(--line);background:var(--white)}
.card-photo{left:0;top:0;width:299px;height:161px}
.card-icon{left:115px;top:127px;width:68px;height:68px;border-radius:50%;background:var(--white);display:flex;align-items:center;justify-content:center}
.card-title{left:0;top:187px;width:299px;text-align:center;font-size:20px;font-weight:500;letter-spacing:.5px}
.card-text{left:30px;top:222px;width:239px;text-align:center;font-size:12.5px;line-height:20px;color:var(--muted)}
.card-btn{left:94px;top:288px;width:111px;height:35px;display:flex;align-items:center;justify-content:center;color:var(--white);font-size:13.5px}

/* footer */
.site-footer{left:0;top:1944px;width:1200px;height:337px;background:var(--footer)}
.footer-col{top:54px}
.footer-col h3{font-size:17px;font-weight:400;color:var(--blue);margin-bottom:14px;letter-spacing:.3px}
.footer-col li{list-style:none;font-size:13.5px;color:#555;line-height:26.5px}
.chat-btn{left:806px;top:93px;width:192px;height:41px;border-radius:21px;background:var(--blue);border:3px solid #7aa9d6;color:var(--white);font-size:17px;display:flex;align-items:center;justify-content:center;gap:7px}
.social{top:158px;display:flex;gap:11px;left:812px}
.social a{width:34px;height:34px;border-radius:50%;background:var(--red)}
.footer-rule{left:134px;top:277px;width:926px;height:1px;background:#dadada}
.copyright{left:138px;top:295px;font-size:12.5px;color:#666}
.legal{left:890px;top:295px;font-size:12.5px;color:#666;width:170px;text-align:right}
</style>
</head>
<body>

<header class="site-header abs">
  <a class="brand abs" href="#"><span class="brand-mark"></span><span class="brand-name">Velmora Sports Foundation</span></a>
  <nav class="main-nav abs">
    <a class="active" style="left:0">Home</a>
    <a style="left:69px">Program</a>
    <a style="left:154px">Donate</a>
    <a style="left:231px">Meet the Team</a>
    <a style="left:364px">Contact us</a>
  </nav>
  <span class="nav-underline abs"></span>
  <a class="btn-donate abs" href="#" style="left:951px;top:40px;width:111px;height:36px">Donate
    <svg viewBox="0 0 24 24"><path d="M12 3c2 3 3 4.5 3 6a3 3 0 0 1-6 0c0-1.5 1-3 3-6z" fill="#fff"/><path d="M2 16c3-1 6-1 9 0h5c1 0 1 1.5 0 1.5h-4M2 20c4 0 8 .5 11 .5s6-2 9-4" stroke="#fff" stroke-width="1.8" fill="none" stroke-linecap="round"/></svg>
  </a>
</header>

<section class="hero abs" role="img" aria-label="Two young soccer players leaping for a ball under stadium lights"></section>
<h1 class="hero-title abs">FINANCIAL HELP TO ATHLETES</h1>
<p class="hero-sub abs">MAURIS LACUS VITAE FELIS VESTIBULUM</p>
<div class="slider-dots abs"><span></span><span></span><span></span><span></span></div>

<section class="about">
  <h2 class="about-title abs">VELMORA SPORTS FOUNDATION</h2>
  <div class="about-text abs">
    <p>Captain &amp; Maritime eleifend libero a tempus libero lectus feugiat felis Morbi diam mauris viverra in gravida eu mattis in ante Morbi eget arcu</p>
    <p>Morbi porta libero id ullamcorper nonummy nibh ligula pulvinar metus eget consectetuer augue nisi quis lacus Ut ac mi quis lacus mollis aliquam Curabitur iaculis tempus eros Curabitur vel mi sit amet &nbsp;per conubia</p>
  </div>
  <a class="btn-donate about-donate abs" href="#">Donate
    <svg viewBox="0 0 24 24"><path d="M12 3c2 3 3 4.5 3 6a3 3 0 0 1-6 0c0-1.5 1-3 3-6z" fill="#fff"/><path d="M2 16c3-1 6-1 9 0h5c1 0 1 1.5 0 1.5h-4M2 20c4 0 8 .5 11 .5s6-2 9-4" stroke="#fff" stroke-width="1.8" fill="none" stroke-linecap="round"/></svg>
  </a>
  <div class="video abs">
    <div class="video-frame abs" role="img" aria-label="Video still of a soccer player kicking in a packed stadium"></div>
    <div class="video-play abs"><svg width="54" height="54" viewBox="0 0 54 54"><path d="M22 17l15 10-15 10z" fill="#111"/></svg></div>
    <div class="video-bar abs">
      <svg width="396" height="28" viewBox="0 0 396 28">
        <path d="M9 9l8 5-8 5z" fill="#ddd"/>
        <rect x="28" y="11" width="272" height="5" rx="2.5" fill="#ccc"/>
        <rect x="28" y="11" width="125" height="5" rx="2.5" fill="#3a8ed6"/>
        <path d="M368 11h4l5-4v14l-5-4h-4z" fill="#ddd"/>
        <path d="M380 10q3 4 0 8" stroke="#ddd" stroke-width="1.5" fill="none"/>
      </svg>
    </div>
  </div>
</section>

<section class="programs abs">
  <span class="programs-rule abs" style="left:487px"></span>
  <h2 class="programs-title abs">Programs</h2>
  <span class="programs-rule abs" style="left:697px"></span>

  <div class="program-photo abs" style="left:152px;top:105px;background:radial-gradient(ellipse 90px 60px at 60% 30%,rgba(230,200,60,.6),transparent 70%),radial-gradient(ellipse 70px 90px at 30% 45%,rgba(60,90,170,.7),transparent 70%),linear-gradient(180deg,#2a3050 0%,#3b4a6a 40%,#3f7a3a 70%,#2e6a2a 100%)" role="img" aria-label="Community club players competing for the ball on a grass pitch"></div>
  <h3 class="program-name abs" style="left:397px;top:124px">Community Clubs</h3>
  <p class="program-text abs" style="left:397px;top:158px">sit amet magna malesuada ultrices Ut nisi erat fermentum vel congue id euismod in elit Fusce ultricies orci ac feugiat suscipit leo massa</p>
  <a class="btn-light abs" href="#" style="left:398px;top:278px">Learn More</a>

  <div class="program-photo abs" style="left:634px;top:105px;background:radial-gradient(ellipse 60px 80px at 50% 40%,rgba(245,245,250,.75),transparent 70%),radial-gradient(ellipse 160px 60px at 50% 78%,rgba(120,200,255,.7),transparent 70%),linear-gradient(180deg,#0d2450 0%,#1d5aa8 55%,#0e2a60 100%)" role="img" aria-label="Individual soccer player striking the ball in a lit stadium"></div>
  <h3 class="program-name abs" style="left:881px;top:124px">Individuals</h3>
  <p class="program-text abs" style="left:881px;top:158px">sit amet magna malesuada ultrices Ut nisi erat fermentum vel congue id euismod in elit Fusce ultricies orci ac feugiat suscipit leo massa</p>
  <a class="btn-light abs" href="#" style="left:881px;top:278px">Learn More</a>
</section>

<article class="card abs" style="left:137px">
  <div class="card-photo abs" style="background:radial-gradient(ellipse 150px 70px at 50% 55%,rgba(205,150,120,.9),transparent 75%),linear-gradient(180deg,#7f9fb8 0%,#5d7d96 60%,#465f74 100%)" role="img" aria-label="Team members joining hands together"></div>
  <div class="card-icon abs"><svg width="46" height="34" viewBox="0 0 46 34" fill="var(--navy)"><circle cx="23" cy="8" r="6"/><path d="M13 33c0-9 4-14 10-14s10 5 10 14z"/><circle cx="9" cy="12" r="4.5"/><path d="M1 33c0-7 3-11 8-11 2 0 3 .5 4 1.5-2 3-3 6-3 9.5z"/><circle cx="37" cy="12" r="4.5"/><path d="M45 33c0-7-3-11-8-11-2 0-3 .5-4 1.5 2 3 3 6 3 9.5z"/></svg></div>
  <h3 class="card-title abs" style="color:var(--blue)">MEET THE TEAM</h3>
  <p class="card-text abs">Donec dictum lectus non odio Cras a ante vitae enim iaculis aliquam Mauris nunc quam venenatis nec</p>
  <a class="card-btn abs" href="#" style="background:var(--navy)">Learn More</a>
</article>

<article class="card abs" style="left:450px">
  <div class="card-photo abs" style="background:radial-gradient(ellipse 110px 60px at 55% 55%,rgba(255,235,120,.95),transparent 75%),linear-gradient(180deg,#e8501c 0%,#f5a623 50%,#6a2a0c 78%,#1e0c06 100%)" role="img" aria-label="Crowd with raised hands against a sunset"></div>
  <div class="card-icon abs"><svg width="52" height="52" viewBox="0 0 52 52"><circle cx="26" cy="26" r="25" fill="var(--red)"/><text x="26" y="27" text-anchor="middle" font-family="Mulish,sans-serif" font-size="18" font-weight="800" fill="#fff">$</text><path d="M12 30q2 10 14 12q12-2 14-12" stroke="#fff" stroke-width="3" fill="none" stroke-linecap="round"/></svg></div>
  <h3 class="card-title abs" style="color:var(--red)">FINANCIAL HELP</h3>
  <p class="card-text abs">Donec dictum lectus non odio Cras a ante vitae enim iaculis aliquam Mauris nunc quam venenatis nec</p>
  <a class="card-btn abs" href="#" style="background:var(--red)">Learn More</a>
</article>

<article class="card abs" style="left:762px">
  <div class="card-photo abs" style="background:radial-gradient(ellipse 55px 50px at 65% 62%,rgba(235,235,235,.85),transparent 75%),linear-gradient(180deg,#2f6a24 0%,#5aa03c 45%,#6bb04a 75%,#4b8c36 100%)" role="img" aria-label="Player's boot resting on a soccer ball at the corner line"></div>
  <div class="card-icon abs"><svg width="52" height="40" viewBox="0 0 52 40"><text x="26" y="32" text-anchor="middle" font-family="Mulish,sans-serif" font-size="32" font-weight="700" fill="var(--sky)">??</text></svg></div>
  <h3 class="card-title abs" style="color:var(--sky)">WHY WE ARE</h3>
  <p class="card-text abs">Donec dictum lectus non odio Cras a ante vitae enim iaculis aliquam Mauris nunc quam venenatis nec</p>
  <a class="card-btn abs" href="#" style="background:var(--sky)">Learn More</a>
</article>

<footer class="site-footer abs">
  <div class="footer-col abs" style="left:140px">
    <h3>INFORMATION</h3>
    <ul><li>About us</li><li>Why We Are</li><li>Our Programs</li><li>Meet the Team</li></ul>
  </div>
  <div class="footer-col abs" style="left:342px">
    <h3>RESOURCES</h3>
    <ul><li>Blogs</li><li>Testimonials</li><li>Donate Now</li><li>Contact Us</li></ul>
  </div>
  <div class="footer-col abs" style="left:543px">
    <h3>CONTACT US</h3>
    <ul><li>410 Harbor Lane Suite B12</li><li>Millbrook, PA 19000</li><li>(555) 014-2000</li><li>info@velmorasports.org</li></ul>
  </div>
  <div class="footer-col abs" style="left:812px">
    <h3>LIVE CHAT NOW</h3>
  </div>
  <a class="chat-btn abs" href="#"><svg width="22" height="18" viewBox="0 0 22 18"><ellipse cx="9" cy="7" rx="8" ry="6" fill="none" stroke="#fff" stroke-width="1.8"/><path d="M4 12l-2 4 5-2" fill="#fff"/></svg>24/7 LIVE CHAT</a>
  <div class="social abs">
    <a href="#" aria-label="Social profile 1"></a>
    <a href="#" aria-label="Social profile 2"></a>
    <a href="#" aria-label="Social profile 3"></a>
    <a href="#" aria-label="Social profile 4"></a>
  </div>
  <div class="footer-rule abs"></div>
  <p class="copyright abs">© 2016 Company Name &nbsp;All right reserved</p>
  <p class="legal abs">Term of Use &nbsp;| &nbsp;Privacy Policy</p>
</footer>

</body>
</html>
```